Fence Contractor Website Design

We are working with Yard Shield. They are a local fencing and automatic gate installer and in need of a new website design.
Some sites to use for inspiration:
https://pelmorfence.example
https://tarvikfence.example
https://www.bristowdecksandfence.example
https://www.railquestinc.example
Thank you for taking the time to consider designing a website for us. We are web developers based in Stockton, CA, USA. Most of our projects go through the same process. Understanding this process may help you win a project with us. We custom-code all of our websites in-house. We don’t have any requirements as to what tools you use for your design, but we prefer Figma files. For any design that we label as four-stars, we send it to the client for review. The client picks the final design they want us to use. Once we complete this process, we will continue to show additional clients all the four-star sites and purchase them later. Your designs will have multiple chances to sell. For better chances of success, we ask that you follow these guidelines.
IMAGES:
If you use any images or icons in the design, we ask that you have a link to the asset so we can purchase the image/icon. Most of the designs we submit do not have the customer’s images on them unless they have some great images. Be creative; show us the feeling you are trying to portray with your image choices. Use any royalty-free site you choose. We subscribe to Veltrix and mainly use their images, but we can purchase images outside of Veltrix.
PLEASE NOTE: we will not submit designs to clients with watermarks on the images.
FONTS:
We ask that you identify the fonts used in the design. This can be done in a message if you want. We typically use Google Fonts and Veltrix Fonts.
CONTENT:
We're always open to different content and ideas. We often submit designs with stock images so the client can see our vision. We typically take pictures after the website launch to use their images with our vision. Lorem Ipsum is fine for paragraphs, but we ask that you write the headers in correct English. We want to be able to show the vision and identify the sections of the website.
INSPIRATION:
We typically add a couple of links in the brief of websites we like to help you get started in your design.
REVISIONS:
We do not often ask for revisions of the designs unless we see something in the design that may not appeal to the client. If there are slight changes that we want to make, we do that in the development process.
FEEDBACK:
We rarely give feedback on designs during the design process. We are working on many website projects and do not have the time to provide feedback. We usually respond if your request is well thought out and asks specific questions, but a note asking “feedback, please” usually goes unanswered.

```html
<!DOCTYPE html>
<html lang="en">
<head>
<meta charset="utf-8">
<title>Yard Shield — Fencing &amp; Gates</title>
<link rel="stylesheet" href="https://fonts.googleapis.com/css2?family=Chakra+Petch:wght@600;700&family=Roboto:wght@400;500;700&display=swap">
<style>
:root{
  --red:#e8141f;
  --navy:#1a2042;
  --ink:#1d2233;
  --text:#4a4f5c;
  --white:#ffffff;
  --head:"Chakra Petch",sans-serif;
  --body:"Roboto",sans-serif;
}
*{box-sizing:border-box;margin:0;padding:0}
html,body{width:1200px;height:4858px;overflow:hidden}
body{position:relative;background:var(--white);font-family:var(--body);color:var(--text)}
.abs{position:absolute}
a{color:inherit;text-decoration:none}

/* header */
.social{display:flex;gap:14px}
.hex-btn{width:30px;height:30px;background:var(--red);clip-path:polygon(25% 3%,75% 3%,100% 50%,75% 97%,25% 97%,0 50%)}
.call{left:828px;top:28px;display:flex;align-items:center;gap:20px}
.call-icon{width:34px;height:30px;background:var(--red);clip-path:polygon(25% 3%,75% 3%,100% 50%,75% 97%,25% 97%,0 50%);display:flex;align-items:center;justify-content:center}
.call small{display:block;font-size:14px;color:var(--ink)}
.call strong{display:block;font-family:var(--head);font-size:22px;color:var(--navy);line-height:1.1}
.navbar{left:117px;top:90px;width:968px;height:90px;background:var(--white);clip-path:polygon(0 0,100% 0,97% 100%,3% 100%);box-shadow:0 4px 10px rgba(0,0,0,.1)}
.nav-link{top:125px;font-size:15px;color:var(--ink)}
.nav-link.active{color:var(--red)}
.brand-plate{left:462px;top:0;width:276px;height:230px;background:var(--white);clip-path:polygon(0 0,100% 0,100% 72%,50% 100%,0 72%)}
.brand-name{left:462px;top:112px;width:276px;text-align:center;font-family:var(--head);font-weight:700;font-size:34px;line-height:40px;color:var(--navy);letter-spacing:1px}

/* hero */
.hero-photo{left:0;top:136px;width:1200px;height:530px;background:linear-gradient(180deg,#2e3a2c 0%,#3d4a3a 40%,#5c625c 75%,#7b7f80 100%)}
.hero-shade{left:0;top:136px;width:1200px;height:530px;background:linear-gradient(180deg,rgba(0,0,0,.25),rgba(0,0,0,.35))}
.hero-title{left:0;top:320px;width:1200px;text-align:center;font-family:var(--head);font-weight:700;font-size:58px;color:var(--white);letter-spacing:1px}
.hero-title span{color:var(--red)}
.hero-sub{left:0;top:394px;width:1200px;text-align:center;font-family:var(--head);font-weight:700;font-size:40px;color:var(--white)}
.hero-text{left:0;top:475px;width:1200px;text-align:center;font-size:18px;line-height:31px;color:var(--white)}
.btn{display:flex;align-items:center;justify-content:center;font-size:14px;font-weight:500;clip-path:polygon(7% 0,93% 0,100% 50%,93% 100%,7% 100%,0 50%)}
.btn-red{background:var(--red);color:var(--white)}
.btn-white{background:var(--white);color:var(--red)}
.btn-navy{background:var(--navy);color:var(--white)}

/* headings */
.sec-title{font-family:var(--head);font-weight:700;font-size:42px;color:var(--navy);line-height:1.2}
.sec-title span{color:var(--red)}
.center{left:0;width:1200px;text-align:center}
.sec-sub{font-size:16px;line-height:30px;color:var(--text)}

/* about */
.about-copy{left:681px;width:408px;font-size:15.5px;line-height:30px;text-align:justify}

/* services */
.svc-card{top:1702px;width:232px;height:406px}
.svc-photo{position:absolute;left:0;top:0;width:100%;height:290px}
.svc-label{position:absolute;left:0;top:290px;width:100%;height:100px;background:var(--navy);clip-path:polygon(0 0,100% 0,100% 60%,50% 100%,0 60%)}
.svc-card.active .svc-label{background:var(--red)}
.svc-card.active .svc-photo{outline:3px solid var(--red);outline-offset:-3px}
.svc-name{position:absolute;left:0;top:304px;width:100%;text-align:center;color:var(--white);font-size:16px}
.svc-icon{position:absolute;left:96px;top:336px}
.svc-bar{position:absolute;left:70px;top:392px;width:92px;height:10px;background:var(--red);clip-path:polygon(0 0,100% 0,50% 100%)}
.svc-card.active .svc-bar{background:var(--navy)}
.dots{display:flex;gap:6px}
.dot{width:10px;height:10px;border-radius:50%;background:#f4b3b6}
.dot.on{background:var(--red)}

/* trust */
.trust-title{left:113px;top:2476px;font-family:var(--head);font-weight:700;font-size:44px;line-height:50px;color:var(--white)}
.trust-list{left:145px;top:2640px;list-style:none}
.trust-list li{display:flex;align-items:center;gap:20px;color:var(--white);font-size:17px;height:40px}
.framed{border:3px solid var(--white);box-shadow:0 6px 18px rgba(0,0,0,.25)}

/* testimonials */
.quote-card{top:3208px;width:464px;height:326px;background:var(--white);box-shadow:0 6px 24px rgba(0,0,0,.08)}
.quote-card.active{border:1.5px solid var(--red)}
.quote-mark{position:absolute;left:48px;top:42px;font-family:Georgia,serif;font-size:150px;line-height:1;color:#f7c6c8}
.quote-text{position:absolute;left:48px;top:110px;width:368px;font-size:16px;line-height:28px;text-align:justify}
.quote-tag{position:absolute;left:48px;top:223px;font-size:16px}
.quote-name{position:absolute;left:48px;top:262px;font-size:15px;font-weight:700;color:var(--navy);text-transform:uppercase}

/* gallery */
.compare{top:3804px;width:476px;height:380px;box-shadow:0 10px 20px rgba(0,0,0,.15)}
.compare .half{position:absolute;top:0;height:100%;width:50%}
.handle{position:absolute;left:219px;top:172px;width:38px;height:38px;border-radius:50%;background:var(--white);display:flex;align-items:center;justify-content:center}

/* footer */
.footer-base{left:0;top:4519px;width:1200px;height:339px;background:var(--navy)}
.foot-head{font-family:var(--head);font-weight:600;font-size:20px;color:var(--white)}
.foot-list{list-style:none;color:var(--white);font-size:14px}
.foot-list li{height:31px;display:flex;align-items:center;gap:18px}
.foot-brand{left:100px;top:4640px;width:240px;text-align:center;font-family:var(--head);font-weight:700;font-size:32px;line-height:40px;color:var(--white)}
.foot-line{left:60px;top:4774px;width:1080px;height:1px;background:rgba(255,255,255,.2)}
.copyright{left:0;top:4826px;width:1200px;text-align:center;color:var(--white);font-size:14px}
</style>
</head>
<body>

<!-- HEADER -->
<div class="social abs" style="left:114px;top:36px">
  <a class="hex-btn" href="#" aria-label="Social profile 1"></a>
  <a class="hex-btn" href="#" aria-label="Social profile 2"></a>
  <a class="hex-btn" href="#" aria-label="Social profile 3"></a>
</div>
<div class="call abs">
  <span class="call-icon"><svg width="16" height="16" viewBox="0 0 24 24" fill="#fff"><path d="M6.6 10.8a15 15 0 0 0 6.6 6.6l2.2-2.2c.3-.3.7-.4 1-.2 1.1.4 2.3.6 3.6.6.6 0 1 .4 1 1V20c0 .6-.4 1-1 1A17 17 0 0 1 3 4c0-.6.4-1 1-1h3.5c.6 0 1 .4 1 1 0 1.3.2 2.5.6 3.6.1.3 0 .7-.2 1z"/></svg></span>
  <div><small>Call Us:</small><strong>+1 555 014 2290</strong></div>
</div>

<!-- HERO -->
<div class="hero-photo abs" role="img" aria-label="Modern house with decorative laser-cut metal fence panels and a paved driveway among evergreen trees"></div>
<div class="hero-shade abs"></div>
<svg class="abs" style="left:0;top:600px" width="1200" height="210" viewBox="0 0 1200 210">
  <polygon points="0,66 0,0 52,0 52,30 600,130 1148,30 1148,0 1200,0 1200,66 600,165" fill="#fff"/>
  <polygon points="52,30 600,130 1148,30 1148,56 600,158 52,56" fill="#e8141f"/>
  <rect x="574" y="134" width="52" height="52" fill="#fff" filter="drop-shadow(0 3px 4px rgba(0,0,0,.2))"/>
  <rect x="590" y="150" width="20" height="20" fill="#e8141f"/>
</svg>

<div class="navbar abs"></div>
<a class="nav-link abs active" style="left:171px" href="#">Home</a>
<a class="nav-link abs" style="left:247px" href="#">About Us</a>
<a class="nav-link abs" style="left:348px" href="#">Services</a>
<a class="nav-link abs" style="left:786px" href="#">Reviews</a>
<a class="nav-link abs" style="left:880px" href="#">Gallery</a>
<a class="nav-link abs" style="left:965px" href="#">Contact Us</a>

<div class="brand-plate abs"></div>
<div class="brand-name abs">YARD SHIELD</div>

<h1 class="hero-title abs">STRONG. <span>SECURE.</span> STYLISH</h1>
<p class="hero-sub abs">FENCES &amp; GATES BUILT TO LAST</p>
<p class="hero-text abs">Serving homeowners and businesses with expert fence installation<br>and automatic gate solutions for over 20 years.</p>
<a class="btn btn-red abs" style="left:383px;top:584px;width:200px;height:40px" href="#">Request a Free Quote</a>
<a class="btn btn-white abs" style="left:615px;top:584px;width:200px;height:40px" href="#">See Our Portfolio</a>

<!-- ABOUT -->
<svg class="abs" style="left:113px;top:887px" width="476" height="548" viewBox="0 0 476 548">
  <polygon points="238,0 476,138 476,410 238,548 0,410 0,138" fill="#1a2042"/>
  <polygon points="170,450 306,450 306,490 238,548 170,490" fill="#e8141f"/>
  <polygon points="238,42 438,156 438,394 238,508 38,394 38,156" fill="#fff"/>
</svg>
<div class="abs" role="img" aria-label="Installer in a blue hard hat fitting a black metal gate" style="left:171px;top:950px;width:360px;height:410px;clip-path:polygon(50% 0,100% 26%,100% 74%,50% 100%,0 74%,0 26%);background:linear-gradient(150deg,#7f98b7 0%,#3d5e8f 40%,#24334f 75%,#6b6f75 100%)"></div>

<h2 class="sec-title abs" style="left:681px;top:940px">YOUR LOCAL<br><span>FENCING EXPERTS</span></h2>
<p class="about-copy abs" style="top:1056px">Yard Shield is a family-owned business serving our community for over two decades. Our team takes pride in craftsmanship, reliability, and delivering fencing and gate solutions built to last.</p>
<p class="about-copy abs" style="top:1211px">Sed ut perspiciatis unde omnis iste natus error sit voluptatem accusantium doloremque laudantium, totam rem aperiam.</p>
<a class="btn btn-red abs" style="left:681px;top:1330px;width:204px;height:42px" href="#">Learn More About Us</a>

<!-- SERVICES -->
<h2 class="sec-title abs center" style="top:1544px">SERVICES <span>WE OFFER</span></h2>
<p class="sec-sub abs center" style="top:1604px">From backyard privacy to commercial security, Yard Shield delivers reliable,<br>custom fencing and gate solutions.</p>

<div class="svc-card abs" style="left:113px">
  <div class="svc-photo" role="img" aria-label="White house with a white picket fence" style="background:linear-gradient(180deg,#b9cde0 0%,#e6ebef 55%,#6f8a55 100%)"></div>
  <div class="svc-label"></div><div class="svc-name">Residential Fencing</div>
  <svg class="svc-icon" width="40" height="40" viewBox="0 0 40 40" fill="none" stroke="#fff" stroke-width="2"><path d="M4 20 20 6l16 14M9 16v20h22V16"/><rect x="16" y="24" width="8" height="12"/></svg>
  <div class="svc-bar"></div>
</div>
<div class="svc-card abs active" style="left:360px">
  <div class="svc-photo" role="img" aria-label="Chain-link security fence lit by floodlights at night" style="background:linear-gradient(180deg,#101318 0%,#2b2a2c 45%,#8a6a3a 62%,#2a2d33 100%)"></div>
  <div class="svc-label"></div><div class="svc-name">Commercial Fencing</div>
  <svg class="svc-icon" width="40" height="40" viewBox="0 0 40 40" fill="none" stroke="#fff" stroke-width="2"><path d="M8 36V8l3-4 3 4v28M18 36V8l3-4 3 4v28M28 36V8l3-4 3 4v28M4 14h34M4 28h34"/></svg>
  <div class="svc-bar"></div>
</div>
<div class="svc-card abs" style="left:608px">
  <div class="svc-photo" role="img" aria-label="Modern home with a sliding automatic driveway gate" style="background:linear-gradient(180deg,#c8d3dc 0%,#d9d9d6 45%,#7e7467 70%,#8d8f8c 100%)"></div>
  <div class="svc-label"></div><div class="svc-name">Automatic Gates</div>
  <svg class="svc-icon" width="40" height="40" viewBox="0 0 40 40" fill="none" stroke="#fff" stroke-width="2"><path d="M4 36V14M36 36V14M4 18c8-10 24-10 32 0M10 36V16M16 36V12M22 36V12M28 36V14M2 36h36"/></svg>
  <div class="svc-bar"></div>
</div>
<div class="svc-card abs" style="left:857px">
  <div class="svc-photo" role="img" aria-label="Hands using a drill to repair a chain-link fence post" style="background:linear-gradient(150deg,#6f8d4c 0%,#5d6b55 40%,#3d4248 60%,#8f7a5e 100%)"></div>
  <div class="svc-label"></div><div class="svc-name">Repairs &amp; Maintenance</div>
  <svg class="svc-icon" width="40" height="40" viewBox="0 0 40 40" fill="none" stroke="#fff" stroke-width="2"><path d="M6 34 22 18M26 6a8 8 0 0 0 8 10l-4 4-6-6zM8 6l26 28M6 10l4-4"/></svg>
  <div class="svc-bar"></div>
</div>
<div class="dots abs" style="left:572px;top:2158px"><span class="dot on"></span><span class="dot"></span><span class="dot"></span><span class="dot"></span></div>

<!-- WHY TRUST -->
<svg class="abs" style="left:0;top:2261px" width="1200" height="692" viewBox="0 0 1200 692">
  <defs><linearGradient id="trustFill" x1="0" y1="0" x2="0" y2="1"><stop offset="0" stop-color="#f0222c"/><stop offset="1" stop-color="#d8121c"/></linearGradient></defs>
  <polygon points="52,132 600,0 1148,132 1148,156 600,24 52,156" fill="#1a2042"/>
  <polygon points="0,156 52,156 600,24 1148,156 1200,156 1200,692 0,692" fill="url(#trustFill)"/>
</svg>
<div class="abs" role="img" aria-label="Faint photo of houses behind a fence, tinted red" style="left:0;top:2400px;width:1200px;height:553px;background:linear-gradient(180deg,rgba(120,0,0,.12),rgba(60,0,0,.18))"></div>
<h2 class="trust-title abs">WHY HOMEOWNERS<br>&amp; BUSINESSES<br>TRUST US</h2>
<ul class="trust-list abs">
  <li><svg width="18" height="18" viewBox="0 0 18 18" fill="none" stroke="#fff" stroke-width="2"><rect x="1" y="1" width="16" height="16" rx="2"/><path d="M5 9l3 3 6-7"/></svg>Licensed &amp; Insured Professionals</li>
  <li><svg width="18" height="18" viewBox="0 0 18 18" fill="none" stroke="#fff" stroke-width="2"><rect x="1" y="1" width="16" height="16" rx="2"/><path d="M5 9l3 3 6-7"/></svg>20+ Years of Local Experience</li>
  <li><svg width="18" height="18" viewBox="0 0 18 18" fill="none" stroke="#fff" stroke-width="2"><rect x="1" y="1" width="16" height="16" rx="2"/><path d="M5 9l3 3 6-7"/></svg>Wide Range of Styles &amp; Materials</li>
  <li><svg width="18" height="18" viewBox="0 0 18 18" fill="none" stroke="#fff" stroke-width="2"><rect x="1" y="1" width="16" height="16" rx="2"/><path d="M5 9l3 3 6-7"/></svg>Warranty on Every Installation</li>
</ul>
<a class="btn btn-navy abs" style="left:113px;top:2814px;width:156px;height:42px" href="#">Explore More</a>
<div class="framed abs" role="img" aria-label="Worker in an orange hard hat installing chain-link fencing" style="left:579px;top:2380px;width:261px;height:435px;background:linear-gradient(160deg,#c47a2a 0%,#6e6a66 30%,#9aa0a6 60%,#b06a2e 100%)"></div>
<div class="framed abs" role="img" aria-label="Dark slatted aluminium gate beside a modern home" style="left:857px;top:2548px;width:232px;height:352px;background:linear-gradient(180deg,#a9b8c8 0%,#3a3f47 35%,#262a31 75%,#8b8d90 100%)"></div>

<!-- TESTIMONIALS -->
<h2 class="sec-title abs center" style="top:3042px">WHAT OUR <span>CUSTOMERS SAY</span></h2>
<p class="sec-sub abs center" style="top:3102px">Quis autem vel eum iure reprehenderit qui in ea voluptate velit esse quam nihil molestiae<br>consequatur, vel illum qui dolorem eum fugiat quo voluptas nulla</p>
<div class="quote-card abs active" style="left:117px">
  <div class="quote-mark">“</div>
  <p class="quote-text">Sed ut perspiciatis unde omnis iste natus error sit voluptatem accusantium doloremque laudantium, totam rem aperiam</p>
  <p class="quote-tag">Eaque ipsa quae ab illo inventore</p>
  <p class="quote-name">Dana Whitlow</p>
</div>
<div class="quote-card abs" style="left:617px">
  <div class="quote-mark">“</div>
  <p class="quote-text">Sed ut perspiciatis unde omnis iste natus error sit voluptatem accusantium doloremque laudantium, totam rem aperiam</p>
  <p class="quote-tag">Eaque ipsa quae ab illo inventore</p>
  <p class="quote-name">Dana Whitlow</p>
</div>
<div class="dots abs" style="left:577px;top:3575px"><span class="dot on" style="background:var(--navy)"></span><span class="dot" style="background:#c9ccd6"></span><span class="dot" style="background:#c9ccd6"></span><span class="dot" style="background:#c9ccd6"></span></div>

<!-- GALLERY -->
<h2 class="sec-title abs center" style="top:3657px">SEE THE <span>DIFFERENCE</span></h2>
<p class="sec-sub abs center" style="top:3717px">Quis autem vel eum iure reprehenderit qui in ea voluptate velit esse quam nihil molestiae<br>consequatur, vel illum qui dolorem eum fugiat quo voluptas nulla</p>
<div class="compare abs" style="left:117px">
  <div class="half" role="img" aria-label="Before: weathered wooden picket fence" style="left:0;background:linear-gradient(180deg,#8a6a48 0%,#6d5238 60%,#9a9a98 100%)"></div>
  <div class="half" role="img" aria-label="After: new dark grey metal panel fence" style="left:50%;background:linear-gradient(180deg,#4d5358 0%,#3b4045 70%,#7d6a50 100%)"></div>
  <span class="handle"><svg width="18" height="12" viewBox="0 0 18 12" fill="none" stroke="#1d2233" stroke-width="2"><path d="M6 1 1 6l5 5M12 1l5 5-5 5"/></svg></span>
</div>
<div class="compare abs" style="left:611px">
  <div class="half" role="img" aria-label="Before: orange temporary barrier fencing on a site" style="left:0;background:linear-gradient(180deg,#9aa3a8 0%,#e07a2a 40%,#c86420 60%,#6e5a44 100%)"></div>
  <div class="half" role="img" aria-label="After: new galvanised chain-link fence" style="left:50%;background:linear-gradient(180deg,#a8aeb2 0%,#7d858a 50%,#5d7a48 100%)"></div>
  <span class="handle"><svg width="18" height="12" viewBox="0 0 18 12" fill="none" stroke="#1d2233" stroke-width="2"><path d="M6 1 1 6l5 5M12 1l5 5-5 5"/></svg></span>
</div>
<a class="btn btn-red abs" style="left:498px;top:4232px;width:204px;height:42px" href="#">View Full Gallery</a>

<!-- FOOTER -->
<svg class="abs" style="left:0;top:4359px" width="1200" height="160" viewBox="0 0 1200 160">
  <polygon points="52,132 600,0 1148,132 1148,160 52,160" fill="#e8141f"/>
  <polygon points="52,160 600,34 1148,160" fill="#1a2042"/>
</svg>
<div class="footer-base abs"></div>
<div class="foot-brand abs">YARD SHIELD</div>

<h3 class="foot-head abs" style="left:417px;top:4522px">QUICK LINKS</h3>
<ul class="foot-list abs" style="left:417px;top:4562px">
  <li><span>»</span>Home</li><li><span>»</span>About Us</li><li><span>»</span>Services</li>
  <li><span>»</span>Reviews</li><li><span>»</span>Gallery</li><li><span>»</span>Contact Us</li>
</ul>

<h3 class="foot-head abs" style="left:647px;top:4522px">CONTACT INFO</h3>
<ul class="foot-list abs" style="left:647px;top:4562px">
  <li><svg width="12" height="14" viewBox="0 0 12 16" fill="#fff"><path d="M6 0a6 6 0 0 0-6 6c0 4.5 6 10 6 10s6-5.5 6-10a6 6 0 0 0-6-6zm0 8.5A2.5 2.5 0 1 1 6 3.5a2.5 2.5 0 0 1 0 5z"/></svg>48 Alder Lane,</li>
  <li><span style="width:12px"></span>Yard Shield Fencing &amp; Gates</li>
  <li><span style="width:12px"></span>United States</li>
  <li style="height:62px;align-items:flex-end;padding-bottom:8px"><svg width="12" height="12" viewBox="0 0 24 24" fill="#fff"><path d="M6.6 10.8a15 15 0 0 0 6.6 6.6l2.2-2.2c.3-.3.7-.4 1-.2 1.1.4 2.3.6 3.6.6.6 0 1 .4 1 1V20c0 .6-.4 1-1 1A17 17 0 0 1 3 4c0-.6.4-1 1-1h3.5c.6 0 1 .4 1 1 0 1.3.2 2.5.6 3.6.1.3 0 .7-.2 1z"/></svg>+1 555 014 2290</li>
  <li><svg width="12" height="10" viewBox="0 0 24 18" fill="none" stroke="#fff" stroke-width="2"><rect x="1" y="1" width="22" height="16"/><path d="M1 1l11 8 11-8"/></svg>info@yardshield.example</li>
</ul>

<h3 class="foot-head abs" style="left:934px;top:4522px">LET'S CONNECT</h3>
<div class="social abs" style="left:934px;top:4570px;gap:16px">
  <a class="hex-btn" href="#" aria-label="Social profile 1"></a>
  <a class="hex-btn" href="#" aria-label="Social profile 2"></a>
  <a class="hex-btn" href="#" aria-label="Social profile 3"></a>
</div>

<div class="foot-line abs"></div>
<a class="btn btn-red abs" style="left:980px;top:4780px;width:106px;height:38px" href="#">↑&nbsp; Go Top</a>
<p class="copyright abs">(C) Copyright 2025 | All Rights Reserved</p>

</body>
</html>
```